Business Card for my New Brokerage

Looking to get a business card design for my new Real Estate Brokerage.
I want it with Picture, Phone Number, Email, Website, Office Address
Name and Designation. Please add logo too.

Target Market(s)

Real Estate Investors or Home Buyers

Industry/Entity Type

Real Estate

Contact Information for Business Card

Name, Email, Phone Number, website, email, office address

Colors
EB3D1F
EC4F4E
F09395
F8D3D4
FCEDEE

Requirements
Must have
• Minimalistic, Clean, Modern, Photo
Nice to have
• White and Red Colors

```html
<!DOCTYPE html>
<html lang="en">
<head>
<meta charset="utf-8">
<title>Ember Realty Inc – Business Card</title>
<link rel="stylesheet" href="https://fonts.googleapis.com/css2?family=Montserrat:wght@400;500;600;700&display=swap">
<style>
  :root {
    --stage: #1d1d1d;
    --paper: #ffffff;
    --brand-red: #dd0000;
    --gold: #d9b965;
    --ink: #4a4a4a;
    --photo-dark: #2a3148;
    --photo-light: #c9d6ea;
    --back-mark: #d2c9c9;
  }
  * { box-sizing: border-box; margin: 0; padding: 0; }
  html, body {
    width: 1200px; height: 1199px; overflow: hidden;
    background: var(--stage);
    font-family: "Montserrat", sans-serif;
  }
  .card {
    position: absolute; left: 195px; width: 800px; height: 435px;
    box-shadow: 0 14px 30px rgba(0,0,0,.55);
    overflow: hidden;
  }
  .card--front { top: 115px; background: var(--paper); }
  .card--back { top: 650px; background: var(--brand-red); }

  .brand-name {
    position: absolute; left: 40px; top: 70px;
    color: var(--brand-red); font-weight: 700; font-size: 38px;
    letter-spacing: 0.5px; line-height: 1;
  }
  .brand-name .sub { font-size: inherit; }

  .accent-bar {
    position: absolute; left: 0; top: 194px; width: 10px; height: 48px;
    background: var(--brand-red);
  }
  .person-name {
    position: absolute; left: 40px; top: 192px;
    color: var(--brand-red); font-weight: 600; font-size: 31px;
    letter-spacing: 1.2px; line-height: 1.2;
  }
  .person-title {
    position: absolute; left: 40px; top: 226px;
    color: var(--ink); font-size: 18px; letter-spacing: 0.4px;
  }
  .address {
    position: absolute; left: 40px; top: 262px;
    color: var(--ink); font-size: 18px; line-height: 26px; letter-spacing: 0.4px;
    font-style: normal;
  }
  .contacts {
    position: absolute; left: 40px; top: 325px; list-style: none;
    color: var(--ink); font-size: 18px; letter-spacing: 0.4px;
  }
  .contacts li { display: flex; align-items: center; height: 26.5px; }
  .contacts svg { width: 14px; height: 14px; margin-right: 8px; flex: none; }

  .portrait {
    position: absolute; left: 474px; top: 9px; width: 326px; height: 380px;
    background: linear-gradient(180deg, var(--paper) 0%, var(--photo-light) 45%, var(--photo-dark) 100%);
  }
  .bands { position: absolute; left: 0; top: 0; width: 800px; height: 435px; }

  .back-name {
    position: absolute; left: 0; right: 0; top: 190px; text-align: center;
    color: var(--back-mark); font-weight: 700; font-size: 62px; letter-spacing: 1px;
  }
</style>
</head>
<body>
  <section class="card card--front">
    <div class="brand-name">Ember Realty Inc</div>

    <div class="portrait" role="img" aria-label="Portrait photo of the broker in a dark blazer and light blue shirt"></div>

    <svg class="bands" viewBox="0 0 800 435" aria-hidden="true">
      <polygon points="0,420 432,420 422,435 0,435" fill="var(--gold)"/>
      <polygon points="475,389 800,389 800,435 428,435" fill="var(--brand-red)"/>
    </svg>

    <div class="accent-bar"></div>
    <h1 class="person-name">DANIEL HARPER</h1>
    <p class="person-title">Founder and President</p>
    <address class="address">1280 Maple Ridge Way<br>Fairview, GA 30418</address>
    <ul class="contacts">
      <li>
        <svg viewBox="0 0 16 16"><path d="M4 1.5l2.3 3-1.4 1.6c.8 1.8 2.2 3.3 4 4.2l1.6-1.4 3 2.3-1.6 2.6C6.5 13.4 2.6 9.5 1.4 4l2.6-2.5z" fill="var(--brand-red)"/></svg>
        +330 555-0142
      </li>
      <li>
        <svg viewBox="0 0 16 16"><rect x="1.5" y="3.5" width="13" height="9" rx="1" fill="none" stroke="var(--brand-red)" stroke-width="1.6"/><path d="M2 4l6 4.5L14 4" fill="none" stroke="var(--brand-red)" stroke-width="1.6"/></svg>
        hello@emberrealtyinc.com
      </li>
      <li>
        <svg viewBox="0 0 16 16"><g fill="none" stroke="var(--brand-red)" stroke-width="1.3"><circle cx="8" cy="8" r="6.5"/><ellipse cx="8" cy="8" rx="3" ry="6.5"/><path d="M1.5 8h13M2.5 4.8h11M2.5 11.2h11"/></g></svg>
        www.emberrealtyinc.com
      </li>
    </ul>
  </section>

  <section class="card card--back">
    <div class="back-name">Ember Realty Inc</div>
  </section>
</body>
</html>
```